Facial Tissue Brand Logo and Design

We would like you to design a Logo for the Facial Tissue Brand "Velora" along with the box design. The pack should indicate the pack size (150 x 2 ply). Also our company logo should be present (attached) along with a barcode. The box size dimensions should be 210mm (L) x 110mm (W) x 70mm (H). We are open to all kinds of nice designs which are attractive but not overdone. Happy designing!

UPDATE:
We appreciate the designs so far... but would also love to see more options in a simple and elegent design style that would look good on a table... please see attached below links for reference purpose:

www.pictovault-example.com/image-photo/cleaning-wipes-isolated-on-white-257770819

www.pictovault-example.com/image-photo/cleaning-wipes-isolated-on-white-155326937

www.pictovault-example.com/image-photo/delicate-female-hands-pulling-tissue-out-1330426586

Happy desgining!

We appreciate the designs so far.. but would like to to see some more options.

```html
<!DOCTYPE html>
<html lang="en">
<head>
<meta charset="utf-8">
<title>Velora Facial Tissue – Box Dieline</title>
<link rel="stylesheet" href="https://fonts.googleapis.com/css2?family=Montserrat:wght@500;600&display=swap">
<style>
  :root {
    --page-bg: #ffffff;
    --flap: #333333;
    --panel: #3a3a3a;
    --pattern-hi: #474747;
    --pattern-lo: #363636;
    --fold: #6a6a6a;
    --ink-light: #ffffff;
    --ink-dark: #2a2a2a;
    --window: #ffffff;
    --thumb-cut: #3f8f5a;
  }
  html, body {
    margin: 0;
    width: 678px;
    height: 1200px;
    overflow: hidden;
    background: var(--page-bg);
  }
  .canvas {
    position: relative;
    width: 678px;
    height: 1200px;
  }
  .dieline {
    position: absolute;
    left: 19px;
    top: 240px;
    width: 639px;
    height: 721px;
  }
  .flap { fill: var(--flap); stroke: var(--fold); stroke-width: 1.5; stroke-dasharray: 5 4; }
  .body-panel { fill: var(--panel); }
  .fold-line { stroke: var(--fold); stroke-width: 1.5; stroke-dasharray: 5 4; }
  .window, .barcode-panel { fill: var(--window); }
  .thumb-cut { fill: none; stroke: var(--thumb-cut); stroke-width: 1.5; stroke-dasharray: 4 3; }
  .brand-name, .tagline, .pack-size, .barcode-label {
    font-family: "Montserrat", sans-serif;
  }
  .brand-name { font-size: 38px; font-weight: 500; letter-spacing: 1px; }
  .tagline { font-size: 11.5px; font-weight: 500; letter-spacing: 0.3px; }
  .pack-size { font-size: 11.5px; font-weight: 600; }
  .barcode-label { font-size: 11.5px; font-weight: 600; fill: var(--ink-dark); }
  .on-dark { fill: var(--ink-light); }
  .on-light { fill: var(--ink-dark); }
  .brand-dot-light { fill: var(--ink-light); }
  .brand-dot-dark { fill: var(--ink-dark); }
</style>
</head>
<body>
<main class="canvas">
  <svg class="dieline" viewBox="60 740 920 1030" xmlns="http://www.w3.org/2000/svg">
    <defs>
      <linearGradient id="patternTone" x1="0" y1="0" x2="1" y2="1">
        <stop offset="0" stop-color="var(--pattern-hi)"/>
        <stop offset="0.25" stop-color="var(--pattern-lo)"/>
        <stop offset="0.5" stop-color="var(--pattern-hi)"/>
        <stop offset="0.75" stop-color="var(--pattern-lo)"/>
        <stop offset="1" stop-color="var(--pattern-hi)"/>
      </linearGradient>
    </defs>

    <!-- top tuck flap -->
    <path class="flap" d="M245 790 L262 755 Q266 745 280 745 L760 745 Q774 745 778 755 L795 790 Z"/>

    <!-- left side flaps -->
    <path class="flap" d="M245 812 L100 812 Q62 812 62 850 L62 1032 Q62 1070 100 1070 L245 1070 Z"/>
    <path class="flap" d="M245 1086 L92 1094 Q62 1096 62 1124 L62 1250 Q62 1276 92 1278 L245 1286 Z"/>
    <path class="flap" d="M245 1298 L100 1298 Q62 1298 62 1336 L62 1494 Q62 1532 100 1532 L245 1532 Z"/>
    <path class="flap" d="M245 1546 L92 1554 Q62 1556 62 1584 L62 1706 Q62 1732 92 1734 L245 1742 Z"/>

    <!-- right side flaps -->
    <path class="flap" d="M795 812 L940 812 Q978 812 978 850 L978 1032 Q978 1070 940 1070 L795 1070 Z"/>
    <path class="flap" d="M795 1086 L948 1094 Q978 1096 978 1124 L978 1250 Q978 1276 948 1278 L795 1286 Z"/>
    <path class="flap" d="M795 1298 L940 1298 Q978 1298 978 1336 L978 1494 Q978 1532 940 1532 L795 1532 Z"/>
    <path class="flap" d="M795 1546 L948 1554 Q978 1556 978 1584 L978 1706 Q978 1732 948 1734 L795 1742 Z"/>

    <!-- main body with geometric pattern area -->
    <rect class="body-panel" x="245" y="790" width="550" height="975"/>
    <rect x="245" y="790" width="550" height="975" fill="url(#patternTone)"
          role="img" aria-label="Subtle grey zigzag chevron and diamond geometric pattern"/>

    <line class="fold-line" x1="245" y1="790" x2="795" y2="790"/>
    <line class="fold-line" x1="245" y1="1078" x2="795" y2="1078"/>
    <line class="fold-line" x1="245" y1="1292" x2="795" y2="1292"/>
    <line class="fold-line" x1="245" y1="1539" x2="795" y2="1539"/>
    <line class="fold-line" x1="245" y1="790" x2="245" y2="1765"/>
    <line class="fold-line" x1="795" y1="790" x2="795" y2="1765"/>

    <!-- back panel: barcode placeholder (upside down) -->
    <rect class="barcode-panel" x="654" y="818" width="116" height="64"/>
    <text class="barcode-label" x="712" y="850" text-anchor="middle" dominant-baseline="central"
          transform="rotate(180 712 850)">bar code</text>

    <!-- back panel brand (upside down) -->
    <g class="back-mark" transform="rotate(180 665 930)">
      <circle class="brand-dot-light" cx="586" cy="912" r="5"/>
      <text class="brand-name on-dark" x="672" y="912" text-anchor="middle" dominant-baseline="central">Velora</text>
      <text class="tagline on-dark" x="665" y="948" text-anchor="middle" dominant-baseline="central">FACIAL TISSUE | ULTRA SOFT</text>
    </g>

    <!-- side panel brand (upside down) -->
    <g class="side-mark" transform="rotate(180 405 1130)">
      <circle class="brand-dot-light" cx="326" cy="1112" r="5"/>
      <text class="brand-name on-dark" x="412" y="1112" text-anchor="middle" dominant-baseline="central">Velora</text>
      <text class="tagline on-dark" x="405" y="1148" text-anchor="middle" dominant-baseline="central">FACIAL TISSUE | ULTRA SOFT</text>
    </g>
    <text class="pack-size on-dark" x="718" y="1110" text-anchor="middle" dominant-baseline="central"
          transform="rotate(180 718 1110)">150 x 2 ply</text>

    <!-- dispensing window -->
    <rect class="window" x="352" y="1335" width="262" height="157" rx="14"/>
    <path class="thumb-cut" d="M352 1365 A22 22 0 0 1 352 1412"/>
    <circle class="brand-dot-dark" cx="440" cy="1425" r="5"/>
    <text class="brand-name on-light" x="525" y="1425" text-anchor="middle" dominant-baseline="central">Velora</text>
    <text class="tagline on-light" x="518" y="1467" text-anchor="middle" dominant-baseline="central">FACIAL TISSUE | ULTRA SOFT</text>

    <!-- front panel -->
    <circle class="brand-dot-light" cx="545" cy="1668" r="5"/>
    <text class="brand-name on-dark" x="630" y="1668" text-anchor="middle" dominant-baseline="central">Velora</text>
    <text class="tagline on-dark" x="630" y="1706" text-anchor="middle" dominant-baseline="central">FACIAL TISSUE | ULTRA SOFT</text>
    <text class="pack-size on-dark" x="310" y="1711" text-anchor="middle" dominant-baseline="central">150 x 2 ply</text>
  </svg>
</main>
</body>
</html>
```